WordPress Design for both website and landing page for an expert

I need a clean and stylish design for my new website. I work as an expert (see attached file WHY HOW WHAT), my product is expert opinion (reports) for company evaluations You can use all of the attached pictures colored or black / white. The person is me, you can add other pictures, if you want. The design should be clean and stylish, so you could use white, black, gray, silver and / or one additional color. I have added an idea about my website, see attached file CONCEPT WEBSITE If you have any more information, please do not hesitate to contact us 'Hesitate to ask me ...

```html
<!DOCTYPE html>
<html lang="de">
<head>
<meta charset="utf-8">
<title>Lukas Behrendt – Expert for Company Valuations</title>
<link rel="stylesheet" href="https://fonts.googleapis.com/css2?family=Montserrat:wght@300;400;500;600;700&display=swap">
<style>
  :root {
    --black: #000;
    --white: #fff;
    --blue: #1d4f9f;
    --nav-blue: #2f6cc4;
    --ink: #2f2f2f;
    --body: #444;
    --line: #d9d9d9;
    --silver: #9a9ea4;
  }
  * { box-sizing: border-box; margin: 0; padding: 0; }
  html, body { width: 1200px; height: 2423px; overflow: hidden; background: var(--white); }
  body { position: relative; font-family: Arial, Helvetica, sans-serif; color: var(--body); }
  .heading { font-family: "Montserrat", sans-serif; }

  /* header */
  .site-header { position: absolute; top: 0; left: 0; width: 1200px; height: 105px; background: var(--black); }
  .brand { position: absolute; left: 113px; top: 32px; display: flex; align-items: center; gap: 12px;
    font-family: "Montserrat", sans-serif; font-weight: 400; font-size: 19px; letter-spacing: 3px; color: var(--white); text-transform: uppercase; }
  .brand-dot { width: 26px; height: 26px; border-radius: 50%; background: var(--silver); }
  .main-nav { position: absolute; top: 44px; left: 0; width: 1200px; }
  .main-nav a { position: absolute; font-family: "Montserrat", sans-serif; font-weight: 600; font-size: 13px;
    color: var(--white); text-decoration: none; letter-spacing: .3px; }
  .main-nav a.active { color: var(--nav-blue); }

  /* hero */
  .hero { position: absolute; top: 105px; left: 0; width: 1200px; height: 565px;
    background: linear-gradient(180deg, #1c6fc0 0%, #3f8fd6 30%, #6aa8dc 48%, #2c3d5c 62%, #243750 78%, #5b6f8a 100%); }
  .hero-title { position: absolute; top: 70px; width: 100%; text-align: center; color: var(--white);
    font-weight: 700; font-size: 35px; letter-spacing: .3px; }
  .hero-sub { position: absolute; top: 124px; width: 100%; text-align: center; color: var(--white);
    font-weight: 300; font-size: 32px; line-height: 42px; }

  /* section titles */
  .section-title { font-weight: 400; font-size: 34px; color: var(--ink); letter-spacing: .5px; }
  .rule { display: block; width: 70px; height: 2px; background: var(--blue); }

  /* why choose us */
  .why { position: absolute; top: 670px; left: 0; width: 1200px; height: 514px; }
  .why .section-title { position: absolute; top: 60px; width: 100%; text-align: center; }
  .why .rule { position: absolute; top: 112px; left: 565px; }
  .feature { position: absolute; top: 150px; width: 306px; height: 300px; border: 1px solid var(--line);
    box-shadow: 0 1px 4px rgba(0,0,0,.12); text-align: center; background: var(--white); }
  .feature-icon { width: 121px; height: 121px; border-radius: 50%; background: var(--blue);
    margin: 23px auto 0; display: flex; align-items: center; justify-content: center; }
  .feature-title { margin-top: 20px; font-weight: 400; font-size: 19px; color: var(--ink); letter-spacing: .5px; }
  .feature-text { margin: 14px auto 0; width: 250px; font-size: 13px; line-height: 26px; color: #333; }

  /* faq */
  .faq { position: absolute; top: 1184px; left: 0; width: 1200px; height: 531px;
    background: linear-gradient(90deg, #eeeeee 0%, #e6e6e6 45%, #d3d0cc 65%, #c9b9a8 85%, #d8d3cc 100%); }
  .faq-inner { position: absolute; left: 113px; top: 0; width: 560px; }
  .faq .section-title { position: absolute; top: 30px; color: var(--blue); }
  .faq .rule { position: absolute; top: 80px; }
  .faq-q-en { position: absolute; top: 97px; font-weight: 500; font-size: 22px; color: #333; white-space: nowrap; }
  .faq-q-de { position: absolute; top: 130px; font-weight: 500; font-size: 19px; color: #333; white-space: nowrap; }
  .faq-item { position: absolute; left: 0; width: 546px; border: 1px solid #b8b8b8; background: rgba(255,255,255,.15);
    padding: 9px 10px 9px 28px; font-size: 13.5px; line-height: 20px; color: #444; }
  .faq-item b { position: absolute; left: 10px; top: 9px; font-family: "Montserrat", sans-serif; font-size: 16px; color: #333; }
  .faq-note { position: absolute; left: 0; width: 560px; font-size: 13.5px; line-height: 26px; color: #444; }

  /* quality promise */
  .quality { position: absolute; top: 1715px; left: 0; width: 1200px; height: 402px; }
  .quality-mark { position: absolute; left: 153px; top: 102px; width: 332px; height: 194px;
    display: flex; align-items: center; justify-content: center; gap: 16px;
    font-family: "Montserrat", sans-serif; font-weight: 400; font-size: 34px; color: var(--silver); letter-spacing: 2px; }
  .quality-mark .dot { width: 34px; height: 34px; border-radius: 50%; background: var(--silver); flex: none; }
  .quality-copy { position: absolute; left: 567px; top: 0; width: 500px; }
  .quality .section-title { position: absolute; top: 44px; white-space: nowrap; }
  .quality .rule { position: absolute; top: 93px; }
  .quality-text { position: absolute; left: 0; width: 500px; font-size: 13px; line-height: 27px; color: #444; }
  .promise-btn { position: absolute; left: 1px; height: 39px; border: 1px solid var(--blue); color: var(--blue);
    font-family: "Montserrat", sans-serif; font-weight: 600; font-size: 13px; line-height: 37px; padding: 0 13px; white-space: nowrap; }

  /* footer */
  .site-footer { position: absolute; top: 2117px; left: 0; width: 1200px; height: 306px; background: var(--black); }
  .footer-brand { position: absolute; top: 62px; width: 100%; display: flex; justify-content: center; align-items: center; gap: 14px;
    font-family: "Montserrat", sans-serif; font-weight: 400; font-size: 26px; letter-spacing: 5px; color: var(--white); text-transform: uppercase; }
  .footer-brand .dot { width: 30px; height: 30px; border-radius: 50%; background: var(--silver); }
  .footer-rule { position: absolute; top: 143px; left: 113px; width: 974px; height: 1px; background: #3a3a3a; }
  .social { position: absolute; top: 167px; width: 58px; height: 58px; border: 1px solid #8a8a8a; border-radius: 50%;
    display: flex; align-items: center; justify-content: center; }
  .copyright { position: absolute; top: 257px; width: 100%; text-align: center; color: var(--white); font-size: 13px; }
</style>
</head>
<body>

<header class="site-header">
  <div class="brand"><span class="brand-dot"></span>Lukas Behrendt</div>
  <nav class="main-nav">
    <a class="active" style="left:480px">HOME</a>
    <a style="left:573px">WHAT I DO</a>
    <a style="left:694px">WHY I DO IT &amp; HOW I DO IT</a>
    <a style="left:909px">ABOUT ME</a>
    <a style="left:1030px">CONTACT</a>
  </nav>
</header>

<section class="hero" role="img" aria-label="Evening city skyline at the river with a TV tower and harbour lights">
  <h1 class="hero-title heading">EXPERT FOR COMPANY VALUATIONS</h1>
  <p class="hero-sub heading">Sie benötigen ein Gutachten zur Ermittlung des<br>Wertes Ihres Unternehmens</p>
</section>

<section class="why">
  <h2 class="section-title heading">WHY CHOOSE US</h2>
  <span class="rule"></span>

  <article class="feature" style="left:113px">
    <div class="feature-icon">
      <svg width="66" height="66" viewBox="0 0 66 66" fill="none" stroke="#fff" stroke-width="3" stroke-linecap="round">
        <circle cx="36" cy="37" r="20"/>
        <path d="M32 12h8M36 12v5M36 37l8-9M8 32h10M6 40h12M10 48h10"/>
      </svg>
    </div>
    <h3 class="feature-title heading">SCHNELL</h3>
    <p class="feature-text">Sie bekommen Ihr Gutachten zeitnah (innerhalb von max. 21 Tagen nach Zugang aller benötigten Unterlagen)</p>
  </article>

  <article class="feature" style="left:447px">
    <div class="feature-icon">
      <svg width="66" height="66" viewBox="0 0 66 66" fill="none" stroke="#fff" stroke-width="3" stroke-linejoin="round" stroke-linecap="round">
        <polygon points="33,4 41,10 51,10 54,20 61,27 57,36 59,46 50,51 45,60 35,58 26,61 19,54 10,50 10,40 5,31 12,24 14,14 24,12"/>
        <path d="M22 33l8 8 15-16"/>
      </svg>
    </div>
    <h3 class="feature-title heading">ZERTIFIZIERT</h3>
    <p class="feature-text">Sie erhalten ein qualifiziertes und belastbares Gutachten von einem zertifizierten Sachverständigen (höchste Akzeptanz Parteien)</p>
  </article>

  <article class="feature" style="left:782px">
    <div class="feature-icon">
      <svg width="70" height="66" viewBox="0 0 70 66">
        <path d="M29 6h12l4 12H25z" fill="#fff"/>
        <path d="M23 24h24l4 12H19z" fill="#fff"/>
        <path d="M17 42h36l4 10H13z" fill="#fff"/>
        <path d="M4 54h62l-6 8H10z" fill="#fff"/>
      </svg>
    </div>
    <h3 class="feature-title heading">VERSTÄNDLICH</h3>
    <p class="feature-text">Ihr Gutachten wird für Sie logisch und nachvollziehbar sein und kein „Fachchinesisch“ enthalten</p>
  </article>
</section>

<section class="faq" role="img" aria-label="Portrait of the valuation expert in a white shirt leaning on a railing in a bright office">
  <div class="faq-inner">
    <h2 class="section-title heading">OUR FAQ’S</h2>
    <span class="rule"></span>
    <p class="faq-q-en heading">What are the buying motives of the customers?</p>
    <p class="faq-q-de heading">Was sind die Kaufmotive der Kunden?</p>

    <div class="faq-item" style="top:176px;height:43px"><b>Q.</b>Sie wollen Anteile Ihres Unternehmens oder ihr gesamtes Unternehmen verkaufen?</div>
    <div class="faq-item" style="top:226px;height:59px"><b>Q.</b>Sie wollen Ihr Unternehmen auf Ihre Erben übertragen und benötigen eine Bewertung für das Finanzamt?</div>
    <div class="faq-item" style="top:292px;height:59px"><b>Q.</b>Sie müssen im Rahmen einer Trennung/Scheidung jemanden ausbezahlen und benötigen eine Bemessungsgrundlage?</div>

    <p class="faq-note" style="top:373px">Lassen Sie Ihr Unternehmen von einem qualifizierten Sachverständigen bewerten und gehen somit vielen (unnötigen) Streitereien aus dem Weg</p>
    <p class="faq-note" style="top:447px">Merke: Die Kosten für ein Gutachten sind immer überproportional günstiger als die Kosten für Rechtsstreitigkeiten. Und das losgelöst psychischen Belastung einer solchen Auseinandersetzung</p>
  </div>
</section>

<section class="quality">
  <div class="quality-mark"><span class="dot"></span>Lukas Behrendt</div>
  <div class="quality-copy">
    <h2 class="section-title heading">MY QUALITY PROMISE</h2>
    <span class="rule"></span>
    <p class="quality-text" style="top:110px">Should the advised date for the preparation of the report be exceeded, you will receive the report free of charge</p>
    <span class="promise-btn" style="top:175px">I WAIVE MY FEE</span>
    <p class="quality-text" style="top:230px">Mein Qualitätsversprechen: Sollte der avisierte Termin für die Erstellung des Gutachtens überschritten werden, erhalten Sie das Gutachten absolut kostenfrei!</p>
    <span class="promise-btn" style="top:302px">ICH VERZICHTE AUF MEIN HONORAR</span>
  </div>
</section>

<footer class="site-footer">
  <div class="footer-brand"><span class="dot"></span>Lukas Behrendt</div>
  <div class="footer-rule"></div>
  <a class="social" style="left:388px" aria-label="Social profile"></a>
  <a class="social" style="left:459px" aria-label="Social profile"></a>
  <a class="social" style="left:530px" aria-label="Social profile"></a>
  <a class="social" style="left:601px" aria-label="Social profile"></a>
  <a class="social" style="left:672px" aria-label="Social profile"></a>
  <a class="social" style="left:745px" aria-label="E-Mail">
    <svg width="18" height="14" viewBox="0 0 18 14" fill="none" stroke="#fff" stroke-width="1.6">
      <rect x="1" y="1" width="16" height="12"/><path d="M1 1l8 7 8-7"/>
    </svg>
  </a>
  <p class="copyright">© Copyrights 2018 - Lukas Behrendt.All Rights Reserved.</p>
</footer>

</body>
</html>
```